Registration Page - Webinar

I need some proposition for a high conversion landing page for a Webinar.
This LP should follow some (minimal) rules:
1 - We need to have a registration box at it
2 - 1, 2 or 3 Keynote Speakers
3 - Featuring Time & Date
4 - All webinars will be free
5 - Title of the webinar
6 - Description of the webinar
7 - Should harmonize with my home page colors (www.themaplehearth.com)

```html
<!DOCTYPE html>
<html lang="en">
<head>
<meta charset="utf-8">
<title>Webinar Registration – The Maple Hearth</title>
<link href="https://fonts.googleapis.com/css2?family=Poppins:wght@400;500;600;700&display=swap" rel="stylesheet">
<style>
:root{
  --pink:#e0005a;
  --navy:#2b1b5c;
  --teal:#2a9cb0;
  --green:#1fa634;
  --sky:#b6e4ec;
  --ink:#1c1c1c;
  --text:#333;
  --dark:#111;
  --field-border:#4fb6c8;
}
*{box-sizing:border-box;margin:0;padding:0}
html,body{width:777px;height:1200px;overflow:hidden}
body{position:relative;background:#fff;font-family:'Poppins',sans-serif;color:var(--text)}
.abs{position:absolute}

/* top navigation */
.topnav{left:0;top:0;width:777px;height:25px;background:var(--pink)}
.topnav ul{list-style:none;display:flex;gap:16px;position:absolute;left:123px;top:6px}
.topnav li{color:#fff;font-size:6.6px;font-weight:500;letter-spacing:.1px}
.social{position:absolute;right:115px;top:8px;display:flex;gap:9px}
.social span{width:8px;height:8px;border-radius:50%;background:#fff;opacity:.9}

/* header */
.header{left:0;top:25px;width:777px;height:53px;background:#fff;border-bottom:1px solid #e4e4e4}
.logo-bulge{left:340px;top:60px;width:97px;height:34px;background:#fff;border-radius:0 0 50px 50px}
.phone-btn{display:flex;align-items:center;gap:5px;background:var(--green);color:#fff;font-weight:600;border-radius:2px}
.phone-btn svg{flex:none}
.hdr-phone{left:155px;top:35px;height:15px;padding:0 5px;font-size:6.4px}
.alt-phones{display:flex;gap:9px;font-size:6.5px;color:var(--navy);align-items:center}
.alt-phones span{display:flex;align-items:center;gap:3px}
.flag{width:10px;height:7px;border-radius:1px;display:inline-block}
.flag.br{background:#2aa84a}
.flag.us{background:linear-gradient(#c8283c 0 50%,#fff 50% 100%);border:0.5px solid #ccc}
.hdr-alt{left:129px;top:55px}
.brand{text-align:center;color:var(--pink);font-weight:700;line-height:1}
.hdr-brand{left:330px;top:42px;width:117px;font-size:15px}
.hdr-brand small{display:block;font-size:7px;letter-spacing:2.5px;margin-top:4px}
.cta{display:flex;align-items:center;gap:5px;color:var(--navy);font-weight:700;line-height:1}
.cta i{display:flex;align-items:center;justify-content:center;border-radius:50%;flex:none}
.cta i.pink{background:var(--pink)}
.cta i.teal{background:var(--teal)}
.hdr-cta{font-size:6.4px;top:40px}
.hdr-cta i{width:21px;height:21px}

/* hero */
.hero{left:0;top:78px;width:777px;height:293px;
  background:linear-gradient(180deg,#3a2a5a 0%,#6a3c6a 28%,#d2643c 52%,#8a3c50 68%,#3a2c58 86%,#22243e 100%)}
.hero h1{position:absolute;left:97px;top:66px;color:#fff;font-size:21.5px;font-weight:700;line-height:28px;letter-spacing:-.2px}

/* registration */
.register{left:444px;top:289px;width:221px;height:494px;background:var(--sky);padding:22px 20px 0 19px}
.register h2{text-align:center;color:var(--ink);font-size:17.5px;font-weight:600;margin-bottom:12px}
.field label{display:block;font-size:7.6px;color:var(--ink);font-weight:500;height:11px}
.field .box{height:25px;background:#fff;border:1px solid var(--field-border);border-radius:2px;margin:5px 0 11px;position:relative}
.field .box.select::after{content:"";position:absolute;right:10px;top:10px;border:3px solid transparent;border-top:4px solid var(--ink)}
.submit{margin-top:1px;height:25px;background:var(--green);color:#fff;font-weight:600;font-size:8.6px;display:flex;align-items:center;justify-content:center;border-radius:2px}

/* speakers */
.speakers-intro{left:111px;top:403px;width:300px}
.speakers-intro .rule{width:58px;height:1px;background:var(--teal);margin-bottom:7px}
.speakers-intro h2{font-size:17px;font-weight:700;color:var(--dark);margin-bottom:9px}
.speakers-intro p{font-size:9.1px;line-height:17px;color:var(--ink)}
.speaker{left:111px;width:310px}
.speaker .portrait{position:absolute;left:0;top:0;width:91px;height:91px;border-radius:50%;border:1px solid var(--pink);padding:3px}
.speaker .portrait div{width:100%;height:100%;border-radius:50%}
.speaker .info{position:absolute;left:109px;top:0;width:210px}
.speaker h3{color:var(--teal);font-size:11.3px;font-weight:600;margin-top:-4px}
.speaker .when{color:var(--navy);font-weight:600;font-size:8.6px;margin-top:4px;word-spacing:1px}
.speaker .when b{margin-left:6px;font-weight:600}
.speaker .price{font-size:8.5px;color:var(--ink);margin-top:2px}
.speaker .price em{font-style:normal;color:var(--pink);font-weight:600}
.speaker h4{font-size:10.4px;font-weight:500;color:var(--ink);margin-top:6px}
.speaker p{font-size:7.8px;line-height:14.6px;color:#444;margin-top:5px}

/* footer */
.skyline{left:0;top:935px;width:777px;height:60px;background:linear-gradient(180deg,#fff 0%,#f0f0f0 60%,#e6e6e6 100%)}
.footer{left:0;top:995px;width:777px;height:173px;background:linear-gradient(180deg,#eee 0%,#fafafa 40%,#fff 100%)}
.addresses{left:111px;top:1006px;width:250px;color:var(--navy)}
.addr{margin-bottom:8px}
.addr h5{display:flex;align-items:center;gap:5px;font-size:8.6px;font-weight:600}
.addr p{font-size:6.8px;line-height:11.6px;margin-top:2px}
.mail{display:flex;align-items:center;gap:4px;font-size:8.6px;font-weight:600;margin-top:2px}
.ftr-brand{left:310px;top:1022px;width:150px;font-size:22px}
.ftr-brand small{display:block;font-size:10px;letter-spacing:3.5px;margin-top:6px}
.ftr-phone{left:509px;top:1005px;height:19px;padding:0 10px;font-size:9.6px;font-weight:500;gap:10px}
.ftr-alt{left:499px;top:1030px}
.ftr-cta{font-size:8.6px;top:1057px}
.ftr-cta i{width:21px;height:21px}
.bottom{left:0;top:1168px;width:777px;height:32px;background:var(--dark);color:#fff}
.bottom .copy{position:absolute;left:111px;top:11px;font-size:7.2px}
.bottom .copy span{color:var(--pink)}
.bottom ul{list-style:none;display:flex;gap:19px;position:absolute;right:111px;top:13px}
.bottom li{font-size:5.6px;font-weight:500}
.bottom li.on{color:var(--pink)}
</style>
</head>
<body>

<nav class="abs topnav">
  <ul><li>HOME</li><li>SOBRE NÓS</li><li>PORTIFÓLIO</li><li>IMÓVEIS</li><li>NOTÍCIAS</li><li>EBOOKS</li><li>CONTATO</li></ul>
  <div class="social"><span></span><span></span><span></span></div>
</nav>

<header class="abs header"></header>
<div class="abs logo-bulge"></div>
<div class="abs phone-btn hdr-phone">
  <svg width="9" height="9" viewBox="0 0 24 24"><path fill="#fff" d="M6.6 10.8a15.1 15.1 0 0 0 6.6 6.6l2.2-2.2c.3-.3.7-.4 1-.2 1.1.4 2.3.6 3.6.6.6 0 1 .4 1 1V20c0 .6-.4 1-1 1A17 17 0 0 1 3 4c0-.6.4-1 1-1h3.5c.6 0 1 .4 1 1 0 1.3.2 2.5.6 3.6.1.3 0 .7-.2 1z"/></svg>
  EUA +(407) 555-0148
</div>
<div class="abs alt-phones hdr-alt">
  <span><i class="flag br"></i>+55 21 5550-1234</span>
  <span><i class="flag us"></i>+1 (855)555-0172</span>
</div>
<div class="abs brand hdr-brand">MAPLE HEARTH<small>LOUNGE</small></div>
<div class="abs cta hdr-cta" style="left:494px">
  <i class="pink"><svg width="11" height="11" viewBox="0 0 24 24"><path fill="none" stroke="#fff" stroke-width="2" d="M4 5h16v10H10l-4 4v-4H4z"/></svg></i>FALE COM UM<br>AGENTE
</div>
<div class="abs cta hdr-cta" style="left:582px">
  <i class="teal"><svg width="11" height="11" viewBox="0 0 24 24"><rect x="4" y="5" width="16" height="15" fill="none" stroke="#fff" stroke-width="2"/><path stroke="#fff" stroke-width="2" d="M4 10h16"/></svg></i>AGENDE UMA<br>CONVERSA
</div>

<section class="abs hero" role="img" aria-label="City skyline along a river with a bridge at sunset">
  <h1>LOREM IPSUM DOLOR SIT AMET<br>CONSECTETUR ADIPISCING ELIT<br>EIUSMOD TEMPOR INCIDID</h1>
</section>

<form class="abs register">
  <h2>Registration</h2>
  <div class="field"><label>First Name*</label><div class="box"></div></div>
  <div class="field"><label>Last Name*</label><div class="box"></div></div>
  <div class="field"><label>Email*</label><div class="box"></div></div>
  <div class="field"><label>Phone*</label><div class="box"></div></div>
  <div class="field"><label>Company Name*</label><div class="box"></div></div>
  <div class="field"><label>Company Website*</label><div class="box"></div></div>
  <div class="field"><label>Country*</label><div class="box select"></div></div>
  <div class="field"><label>Are You an Advertise or Marketing Agency*?</label><div class="box select"></div></div>
  <div class="submit">REGISTER FOR WEBINAR</div>
</form>

<section class="abs speakers-intro">
  <div class="rule"></div>
  <h2>SPEAKERS</h2>
  <p>Lorem ipsum dolor sit amet, consectetur adipiscing elit, sed do eiu smod tempor incididunt ut labore et dolore magna aliqua enim ad minim veniam, quis nostrud exercitation ullamco</p>
</section>

<article class="abs speaker" style="top:514px">
  <div class="portrait"><div role="img" aria-label="Portrait of speaker Jessika Cindy" style="background:linear-gradient(160deg,#8cc3e0,#3d6fa6)"></div></div>
  <div class="info">
    <h3>JESSIKA CINDY</h3>
    <div class="when">Time : 02 pm to 5pm <b>Date : April 15 2020</b></div>
    <div class="price">Price: <em>Free</em></div>
    <h4>Lorem ipsum dolor sit ametonse</h4>
    <p>Lorem ipsum dolor sit amet, consectetur adipiscig elit, sed do eiuod tempor incididunt ut labore etolr emagna aliqua enim ad minim veniam.</p>
  </div>
</article>

<article class="abs speaker" style="top:650px">
  <div class="portrait"><div role="img" aria-label="Portrait of speaker Jhon Smith" style="background:linear-gradient(160deg,#5a6470,#e0b030)"></div></div>
  <div class="info">
    <h3>JHON SMITH</h3>
    <div class="when">Time : 02 pm to 5pm <b>Date : April 15 2020</b></div>
    <div class="price">Price: <em>Free</em></div>
    <h4>Lorem ipsum dolor sit ametonse</h4>
    <p>Lorem ipsum dolor sit amet, consectetur adipiscig elit, sed do eiuod tempor incididunt ut labore etolr emagna aliqua enim ad minim veniam.</p>
  </div>
</article>

<article class="abs speaker" style="top:792px">
  <div class="portrait"><div role="img" aria-label="Portrait of speaker Earin Signsk" style="background:linear-gradient(160deg,#ececec,#8fb2d8)"></div></div>
  <div class="info">
    <h3>EARIN SIGNSK</h3>
    <div class="when">Time : 02 pm to 5pm <b>Date : April 15 2020</b></div>
    <div class="price">Price: <em>Free</em></div>
    <h4>Lorem ipsum dolor sit ametonse</h4>
    <p>Lorem ipsum dolor sit amet, consectetur adipiscig elit, sed do eiuod tempor incididunt ut labore etolr emagna aliqua enim ad minim veniam.</p>
  </div>
</article>

<div class="abs skyline" role="img" aria-label="Faint grey city skyline illustration"></div>
<footer class="abs footer"></footer>

<div class="abs addresses">
  <div class="addr">
    <h5><svg width="6" height="8" viewBox="0 0 12 16"><path fill="#e0005a" d="M6 0a6 6 0 0 0-6 6c0 4.5 6 10 6 10s6-5.5 6-10a6 6 0 0 0-6-6zm0 8.5a2.5 2.5 0 1 1 0-5 2.5 2.5 0 0 1 0 5z"/></svg>Harbor Point Plaza</h5>
    <p>2º Piso, Av. das Palmeiras 1200,<br>Bairro Novo - RJ - Brasil</p>
  </div>
  <div class="addr">
    <h5><svg width="6" height="8" viewBox="0 0 12 16"><path fill="#e0005a" d="M6 0a6 6 0 0 0-6 6c0 4.5 6 10 6 10s6-5.5 6-10a6 6 0 0 0-6-6zm0 8.5a2.5 2.5 0 1 1 0-5 2.5 2.5 0 0 1 0 5z"/></svg>Shopping Jardim Azul</h5>
    <p>Av. Das Acácias, 3100 sala 210 Vila Clara<br>- São Paulo - Brasil</p>
  </div>
  <div class="addr">
    <h5><svg width="6" height="8" viewBox="0 0 12 16"><path fill="#e0005a" d="M6 0a6 6 0 0 0-6 6c0 4.5 6 10 6 10s6-5.5 6-10a6 6 0 0 0-6-6zm0 8.5a2.5 2.5 0 1 1 0-5 2.5 2.5 0 0 1 0 5z"/></svg>Orlando</h5>
    <p>4820 Lakeview Grande Avenue, Suite 210, Orlando, EUA</p>
  </div>
  <div class="mail"><svg width="10" height="7" viewBox="0 0 20 14"><rect width="20" height="14" fill="#e0005a"/><path d="M0 0l10 8 10-8" fill="none" stroke="#fff" stroke-width="1.5"/></svg>contact@themaplehearth.com</div>
</div>

<div class="abs brand ftr-brand">MAPLE HEARTH<small>LOUNGE</small></div>

<div class="abs phone-btn ftr-phone">
  <svg width="11" height="11" viewBox="0 0 24 24"><path fill="#fff" d="M6.6 10.8a15.1 15.1 0 0 0 6.6 6.6l2.2-2.2c.3-.3.7-.4 1-.2 1.1.4 2.3.6 3.6.6.6 0 1 .4 1 1V20c0 .6-.4 1-1 1A17 17 0 0 1 3 4c0-.6.4-1 1-1h3.5c.6 0 1 .4 1 1 0 1.3.2 2.5.6 3.6.1.3 0 .7-.2 1z"/></svg>
  EUA +(407) 555-0148
</div>
<div class="abs alt-phones ftr-alt" style="font-size:7.2px">
  <span><i class="flag br"></i>+55 21 5550-1234</span>
  <span><i class="flag us"></i>+1 (855)555-0172</span>
</div>
<div class="abs cta ftr-cta" style="left:491px">
  <i class="pink"><svg width="11" height="11" viewBox="0 0 24 24"><path fill="none" stroke="#fff" stroke-width="2" d="M4 5h16v10H10l-4 4v-4H4z"/></svg></i>FALE COM UM<br>AGENTE
</div>
<div class="abs cta ftr-cta" style="left:578px">
  <i class="teal"><svg width="11" height="11" viewBox="0 0 24 24"><rect x="4" y="5" width="16" height="15" fill="none" stroke="#fff" stroke-width="2"/><path stroke="#fff" stroke-width="2" d="M4 10h16"/></svg></i>AGENDE UMA<br>CONVERSA
</div>

<div class="abs bottom">
  <div class="copy">© 2020 - THE MAPLE HEARTH BY <span>NORTHPIXEL</span></div>
  <ul><li class="on">HOME</li><li>IMÓVEIS</li><li>NOTÍCIAS</li><li>CONTATO</li><li>TERMS OF USE</li></ul>
</div>

</body>
</html>
```